Business Card Design Project - del varosi group

dear Sirs

we need business card design for our group ( DEL Varosi Group ) , i have got the Logo design of our group from pixel harbor in previous , so all need details relating to our group i think available with you, as well as the the chosen logo design

we hope to provide us with business card logo that to be appropaite and satisfactory to us .

thanks

note : logo design of our group is attached .
Updates

Reason: please extend the deadline of my project for additional 15 days because i didn't received appropriate design for our gruop yet . kindly beaware that i have received 77 design till now , supossed to send me 200-250 design at least . thanks

Target Market(s)

contents

name : Kerem EL Nadiri

position : Operation Manager

Industry/Entity Type

Business

Requirements
Must have

• person name

group logo
Nice to have
• logo color matching with back background

```html
<!DOCTYPE html>
<html lang="en">
<head>
<meta charset="utf-8">
<title>DEL Varosi Group – Business Card</title>
<link rel="stylesheet" href="https://fonts.googleapis.com/css2?family=Open+Sans:wght@400;600;700&display=swap">
<style>
  :root {
    --stage: #b8902c;
    --card-white: #ffffff;
    --navy: #0f4a8a;
    --deep-navy: #0b2f63;
    --blue: #1a78b6;
    --gold: #c39a45;
    --gold-light: #e6cb80;
    --gold-dark: #c0922e;
    --ink: #1a1a1a;
  }
  * { margin: 0; padding: 0; box-sizing: border-box; }
  html, body { width: 1200px; height: 686px; overflow: hidden; }
  body {
    position: relative;
    background: var(--stage);
    font-family: "Open Sans", Arial, sans-serif;
  }
  .card {
    position: absolute;
    width: 523px;
    height: 298px;
  }
  .card-front { left: 64px; top: 129px; background: var(--card-white); }
  .card-back {
    left: 611px; top: 298px;
    background: radial-gradient(ellipse at 52% 50%, var(--gold-light) 0%, #d8b458 45%, var(--gold-dark) 100%);
  }

  .brand {
    position: absolute;
    display: flex;
    align-items: center;
    gap: 10px;
    color: var(--navy);
    font-weight: 600;
    white-space: nowrap;
  }
  .brand-mark { display: block; background: var(--navy); }
  .card-front .brand { left: 38px; top: 48px; font-size: 25px; }
  .card-front .brand-mark { width: 14px; height: 14px; }
  .card-back .brand { left: 100px; top: 132px; font-size: 31px; }
  .card-back .brand-mark { width: 17px; height: 17px; }

  .holder {
    position: absolute; left: 48px; top: 127px;
    display: flex; align-items: center;
  }
  .holder-name { color: var(--blue); font-weight: 700; font-size: 15px; }
  .holder-role {
    color: var(--gold); font-weight: 700; font-size: 11.5px;
    margin-left: 7px; padding-left: 7px;
    border-left: 1px solid #555;
    line-height: 15px;
  }

  .contacts {
    position: absolute; left: 46px; top: 152px;
    list-style: none;
    font-size: 12.5px; color: var(--ink);
  }
  .contacts li { display: flex; align-items: center; height: 17.5px; }
  .contacts svg { width: 12px; height: 12px; margin-right: 4px; fill: var(--blue); }

  .address {
    position: absolute; left: 47px; top: 246px;
    font-size: 12.5px; line-height: 15px; color: var(--ink);
    font-style: normal;
  }

  .emblem-area {
    position: absolute; left: 304px; top: 152px;
    width: 190px; height: 128px;
    background: linear-gradient(100deg, #ecd592 0%, #d8ad63 45%, #1f3d6e 100%);
    opacity: 0.85;
  }
</style>
</head>
<body>

<section class="card card-front">
  <div class="brand"><span class="brand-mark"></span>DEL Varosi Group</div>

  <div class="holder">
    <span class="holder-name">Kerem EL Nadiri</span>
    <span class="holder-role">Operation Manager</span>
  </div>

  <ul class="contacts">
    <li><svg viewBox="0 0 24 24"><path d="M6.6 10.8a15 15 0 0 0 6.6 6.6l2.2-2.2a1 1 0 0 1 1-.25 11 11 0 0 0 3.6.6 1 1 0 0 1 1 1V20a1 1 0 0 1-1 1A17 17 0 0 1 3 4a1 1 0 0 1 1-1h3.5a1 1 0 0 1 1 1 11 11 0 0 0 .6 3.6 1 1 0 0 1-.25 1z"/></svg>(TF)123-456-7890</li>
    <li><svg viewBox="0 0 24 24"><path d="M6.6 10.8a15 15 0 0 0 6.6 6.6l2.2-2.2a1 1 0 0 1 1-.25 11 11 0 0 0 3.6.6 1 1 0 0 1 1 1V20a1 1 0 0 1-1 1A17 17 0 0 1 3 4a1 1 0 0 1 1-1h3.5a1 1 0 0 1 1 1 11 11 0 0 0 .6 3.6 1 1 0 0 1-.25 1z"/></svg>123-456-7890</li>
    <li><svg viewBox="0 0 24 24"><path d="M6 2h10v6H6zM3 9h18v9h-3v4H6v-4H3zm5 7v4h8v-4z"/></svg>123-456-7890</li>
    <li><svg viewBox="0 0 24 24"><path d="M2 5h20v14H2zm2 2v.5l8 5 8-5V7z"/></svg>name@website.com</li>
    <li><svg viewBox="0 0 24 24"><path d="M12 2a10 10 0 1 0 0 20 10 10 0 0 0 0-20zm6.9 6h-3a15 15 0 0 0-1.3-3.9A8 8 0 0 1 18.9 8zM12 4c.8 1.2 1.5 2.5 1.9 4h-3.8c.4-1.5 1.1-2.8 1.9-4zM4.3 14a8 8 0 0 1 0-4h3.4a16 16 0 0 0 0 4zm.8 2h3a15 15 0 0 0 1.3 3.9A8 8 0 0 1 5.1 16zm3-8h-3a8 8 0 0 1 4.3-3.9A15 15 0 0 0 8.1 8zM12 20c-.8-1.2-1.5-2.5-1.9-4h3.8c-.4 1.5-1.1 2.8-1.9 4zm2.3-6H9.7a14 14 0 0 1 0-4h4.6a14 14 0 0 1 0 4zm.3 5.9a15 15 0 0 0 1.3-3.9h3a8 8 0 0 1-4.3 3.9zm1.7-5.9a16 16 0 0 0 0-4h3.4a8 8 0 0 1 0 4z"/></svg>www.website.com</li>
  </ul>

  <address class="address">Street name City<br>State, zip code</address>

  <div class="emblem-area" role="img" aria-label="Large brand emblem decoration area"></div>
</section>

<section class="card card-back">
  <div class="brand"><span class="brand-mark"></span>DEL Varosi Group</div>
</section>

</body>
</html>
```